Budget Brand Responsive Website

Flat vector style website needed for value based IT support company. looking for clean, illustration intensive based design. Current test site can be found at www.bright-mend.co.uk and holding page it www.brightmend.co.uk this will show text and services, please feel free to use placeholder text if you think we need alternative text in places. Emphasis should be on low cost support and services listed on the site, would be nice to see costs in bold images. important colors are the blue, orange and white, see holding page and attached image of an advert

It Company

```html
<!DOCTYPE html>
<html lang="en">
<head>
<meta charset="utf-8">
<title>Bright Mend – Easy and Affordable Tech</title>
<link href="https://fonts.googleapis.com/css2?family=Open+Sans:wght@400;600;700&family=Roboto:wght@300;400;500;700&display=swap" rel="stylesheet">
<style>
:root{
  --blue:#2f4b8c;
  --blue-dark:#243a6e;
  --orange:#e8761c;
  --ink:#333a45;
  --muted:#6b7280;
  --lavender:#e4e6f2;
  --light:#f1f2f5;
  --line:#d8dbe3;
  --dark:#1d1f24;
  --white:#ffffff;
}
*{box-sizing:border-box;margin:0;padding:0}
html,body{width:1200px;height:3064px;overflow:hidden;background:var(--white)}
body{font-family:"Open Sans",Arial,sans-serif;color:var(--ink);position:relative}
.section{position:absolute;left:0;width:1200px}
.title{font-family:"Roboto",Arial,sans-serif;font-weight:700;color:var(--blue);font-size:30px;text-align:center;letter-spacing:.5px;text-transform:uppercase}
.btn{display:inline-block;background:var(--orange);color:var(--white);font-family:"Roboto",Arial,sans-serif;font-weight:700;font-size:14px;padding:10px 22px;letter-spacing:.5px}
.btn-blue{background:var(--blue)}
.wordmark{font-family:"Roboto",Arial,sans-serif;font-weight:700;color:var(--blue);letter-spacing:.5px}
/* header */
.site-header{top:0;height:56px;background:var(--white);display:flex;align-items:center;justify-content:space-between;padding:0 60px 0 72px}
.site-header .wordmark{font-size:26px}
.nav{display:flex;gap:34px;font-family:"Roboto",Arial,sans-serif;font-size:13px;font-weight:500;color:var(--ink)}
/* hero */
.hero{top:56px;height:448px;background:linear-gradient(180deg,#2b2f36 0%,#4a5058 45%,#1c1f24 100%);color:var(--white);text-align:center}
.hero-photo{position:absolute;inset:0;background:radial-gradient(ellipse at 60% 70%,rgba(120,130,140,.45),rgba(0,0,0,0) 60%)}
.hero h1{position:absolute;top:130px;width:100%;font-family:"Roboto",Arial,sans-serif;font-weight:400;font-size:66px;line-height:72px}
.hero h1 .accent{color:var(--orange);font-weight:700}
.hero p{position:absolute;top:300px;width:100%;font-family:"Roboto",Arial,sans-serif;font-size:30px;line-height:36px}
.hero .arrow{position:absolute;top:210px}
/* about */
.about{top:504px;height:384px;text-align:center}
.about .title{margin-top:96px}
.about p{width:1040px;margin:26px auto 0;font-size:13px;line-height:21px;color:var(--muted)}
.about .btn{margin-top:26px}
/* services */
.services{top:888px;height:492px;background:var(--lavender)}
.services .title{margin-top:44px}
.service-grid{position:absolute;top:116px;left:80px;width:1040px;display:grid;grid-template-columns:repeat(3,1fr);gap:36px 26px}
.service-card{background:var(--white);height:160px;display:flex;padding:26px 18px;gap:18px}
.service-icon{flex:0 0 64px;height:64px;border-radius:50%;background:#3d4048;display:flex;align-items:center;justify-content:center}
.service-card h3{font-family:"Roboto",Arial,sans-serif;font-size:15px;font-weight:700;color:var(--blue);margin-bottom:8px}
.service-card ul{list-style:none;font-size:11.5px;line-height:18px;color:var(--muted)}
.service-card li::before{content:"✓ ";color:var(--orange);font-weight:700}
.service-card .more{font-size:11px;font-weight:700;color:var(--orange);margin-top:4px;display:block}
/* pricing */
.pricing{top:1380px;height:488px}
.pricing .title{margin-top:32px;font-size:28px}
.price-table{position:absolute;top:104px;left:80px;width:1040px;display:grid;grid-template-columns:260px repeat(3,1fr)}
.price-col{text-align:center;background:var(--white);border:1px solid var(--line);border-left:none}
.price-col .head{height:120px;padding-top:38px;background:#e9ebf1}
.price-col .head h3{font-family:"Roboto",Arial,sans-serif;font-size:22px;font-weight:700;color:var(--ink)}
.price-col .head span{font-size:12px;color:var(--muted)}
.price-col .row{height:52px;line-height:52px;font-size:13px;color:var(--ink);border-top:1px solid var(--line)}
.price-col .foot{height:72px;padding-top:18px;border-top:1px solid var(--line)}
.price-col.featured{border:none;background:#fbeee2;margin-top:-28px}
.price-col.featured .head{background:var(--orange);height:148px;padding-top:56px}
.price-col.featured .head h3{color:var(--white);font-size:26px}
.price-col.featured .head span{color:var(--white)}
.price-col.featured .row,.price-col.featured .foot{border-top-color:#efd3bb}
/* contracts band */
.contracts{top:1868px;height:300px;background:var(--dark);color:var(--white);text-align:center}
.contracts h2{margin-top:58px;font-family:"Roboto",Arial,sans-serif;font-size:30px;font-weight:700}
.contracts p{width:960px;margin:22px auto 0;font-size:12.5px;line-height:20px;color:#c9ccd2}
.contracts .call{margin-top:30px;font-family:"Roboto",Arial,sans-serif;font-size:28px;font-weight:700}
.contracts .call span{color:var(--orange)}
/* support band */
.support-band{top:2168px;height:316px;background:linear-gradient(135deg,#9aa3ae 0%,#cfd4da 50%,#8d96a2 100%)}
.info-box{position:absolute;background:var(--blue);color:var(--white);padding:40px 30px}
.info-box h2{font-family:"Roboto",Arial,sans-serif;font-size:26px;font-weight:500;margin-bottom:16px;text-align:center}
.info-box p{font-size:11.5px;line-height:18px;text-align:center;color:#dfe5f2}
.info-left{top:24px;left:72px;width:388px;height:268px}
.info-right{top:24px;left:560px;width:600px;height:268px;background:var(--blue-dark)}
/* map */
.map{top:2484px;height:180px;background:linear-gradient(160deg,#b8c7b0 0%,#d9ddd2 40%,#a9bccb 75%,#8fa7bd 100%)}
.offices{position:absolute;top:40px;left:240px;width:760px;height:108px;background:var(--white);display:grid;grid-template-columns:repeat(4,1fr);padding:16px 18px;gap:14px}
.office h4{font-family:"Roboto",Arial,sans-serif;font-size:13px;font-weight:700;color:var(--ink);margin-bottom:4px}
.office p{font-size:11px;line-height:16px;color:var(--muted)}
/* contact */
.contact{top:2664px;height:400px;background:var(--light)}
.contact h2{font-family:"Roboto",Arial,sans-serif;font-size:24px;font-weight:700;color:var(--blue);text-transform:uppercase}
.connect{position:absolute;top:36px;left:72px;width:300px}
.socials{display:flex;gap:10px;margin-top:18px}
.socials span{width:30px;height:30px;border-radius:50%;background:var(--orange)}
.connect .wordmark{margin-top:28px;font-size:30px}
.connect small{display:block;margin-top:22px;font-size:11px;line-height:17px;color:var(--muted)}
.contact-form{position:absolute;top:36px;left:400px;width:720px}
.fields{margin-top:18px;display:grid;grid-template-columns:1fr 1fr;gap:14px}
.field{background:var(--white);border:1px solid var(--line);height:40px;padding:10px 14px;font-size:13px;color:#9aa0aa}
.field.message{grid-column:1/3;height:140px}
.contact-form .btn{float:right;margin-top:16px;padding:12px 26px}
.legal{position:absolute;bottom:14px;right:60px;font-size:10px;color:var(--muted)}
</style>
</head>
<body>

<header class="section site-header">
  <div class="wordmark">BRIGHT MEND</div>
  <nav class="nav"><span>HOME</span><span>ABOUT</span><span>SERVICES</span><span>SUPPORT</span><span>CONTACT</span></nav>
</header>

<section class="section hero">
  <div class="hero-photo" role="img" aria-label="Photo of a person typing on a laptop keyboard in a dark office"></div>
  <h1>We Make <span class="accent">Tech</span><br>Easy and Affordable</h1>
  <p>We Help Our Clients Increase Productivity<br>Whilst Reducing Cost</p>
  <svg class="arrow" style="left:70px" width="24" height="48" viewBox="0 0 24 48"><polyline points="20,4 4,24 20,44" fill="none" stroke="#fff" stroke-width="3"/></svg>
  <svg class="arrow" style="right:70px" width="24" height="48" viewBox="0 0 24 48"><polyline points="4,4 20,24 4,44" fill="none" stroke="#fff" stroke-width="3"/></svg>
</section>

<section class="section about">
  <h2 class="title">About Bright Mend</h2>
  <p>Bright Mend is a market leading Managed Service Provider (MSP). With years of industry experience, our commitment to delivering leading technologies combined with a focus on quality service delivery has been one of the critical success factors in our continued and healthy growth. We have a portfolio of Support Services and Product offerings to suit the dynamics of our client base. We have maintained this proactive and flexible approach which has attracted many of our loyal clients and has continued to strategically align ourselves with leading global vendors.</p>
  <span class="btn">READ MORE</span>
</section>

<section class="section services">
  <h2 class="title">Our Services</h2>
  <div class="service-grid">
    <div class="service-card">
      <div class="service-icon"><svg width="30" height="30" viewBox="0 0 30 30"><circle cx="15" cy="15" r="10" fill="none" stroke="#fff" stroke-width="3"/><circle cx="15" cy="15" r="4" fill="#fff"/></svg></div>
      <div><h3>SUPPORT</h3><ul><li>Unlimited Remote Support</li><li>Monitoring, Auditing &amp; more</li><li>All from £8.00 a month</li></ul><span class="more">READ MORE</span></div>
    </div>
    <div class="service-card">
      <div class="service-icon"><svg width="30" height="30" viewBox="0 0 30 30"><path d="M7 5l5 0 2 6-3 2c1 3 4 6 7 7l2-3 6 2 0 5c-12 1-20-7-19-19z" fill="#fff"/></svg></div>
      <div><h3>VOICE</h3><ul><li>VoIP Telephone Systems</li><li>Telephone Lines</li><li>SIP Trunking &amp; more</li></ul><span class="more">READ MORE</span></div>
    </div>
    <div class="service-card">
      <div class="service-icon"><svg width="30" height="30" viewBox="0 0 30 30"><circle cx="15" cy="15" r="11" fill="none" stroke="#fff" stroke-width="2.5"/><ellipse cx="15" cy="15" rx="5" ry="11" fill="none" stroke="#fff" stroke-width="2"/><line x1="4" y1="15" x2="26" y2="15" stroke="#fff" stroke-width="2"/></svg></div>
      <div><h3>INTERNET</h3><ul><li>Business Broadband</li><li>Leased Lines</li><li>Fibre Broadband</li></ul><span class="more">READ MORE</span></div>
    </div>
    <div class="service-card">
      <div class="service-icon"><svg width="30" height="30" viewBox="0 0 30 30"><rect x="7" y="13" width="16" height="12" fill="#fff"/><path d="M10 13v-4a5 5 0 0 1 10 0v4" fill="none" stroke="#fff" stroke-width="3"/></svg></div>
      <div><h3>SECURITY</h3><ul><li>Encryption</li><li>Antivirus &amp; Anti-Malware</li><li>Patch Management Software</li></ul><span class="more">READ MORE</span></div>
    </div>
    <div class="service-card">
      <div class="service-icon"><svg width="30" height="30" viewBox="0 0 30 30"><rect x="6" y="5" width="18" height="8" fill="#fff"/><rect x="6" y="17" width="18" height="8" fill="#fff"/></svg></div>
      <div><h3>HOSTING</h3><ul><li>Hosted Email</li><li>Cloud Office Suite</li><li>Email Protection</li></ul><span class="more">READ MORE</span></div>
    </div>
    <div class="service-card">
      <div class="service-icon"><svg width="32" height="30" viewBox="0 0 32 30"><path d="M8 23a6 6 0 0 1 0-12 8 8 0 0 1 15-1 6.5 6.5 0 0 1 1 13z" fill="#fff"/></svg></div>
      <div><h3>CLOUD</h3><ul><li>Backup and DR</li><li>Virtual Desktops</li><li>Virtual Private Servers</li></ul><span class="more">READ MORE</span></div>
    </div>
  </div>
</section>

<section class="section pricing">
  <h2 class="title">Pricing For Our Most Popular Services</h2>
  <div class="price-table">
    <div class="price-col featured">
      <div class="head"><h3>SUPPORT</h3><span>Unlimited Monthly Remote Support</span></div>
      <div class="row">Workstations £8.00</div>
      <div class="row">Network Kit £20.00</div>
      <div class="row">Servers £40.00</div>
      <div class="foot"><span class="btn btn-blue">MORE DETAILS</span></div>
    </div>
    <div class="price-col">
      <div class="head"><h3>VOICE</h3><span>Lower Phone And Call Charges</span></div>
      <div class="row">PBX from £40.00</div>
      <div class="row">Line rental from £11.00</div>
      <div class="row">Phones numbers from £5.00</div>
      <div class="foot"><span class="btn btn-blue">MORE DETAILS</span></div>
    </div>
    <div class="price-col">
      <div class="head"><h3>HOSTING</h3><span>Flexible And Secure</span></div>
      <div class="row">Email Archiving from £3.00</div>
      <div class="row">Email Protection from £1.00</div>
      <div class="row">Office Suite from £3.10</div>
      <div class="foot"><span class="btn btn-blue">MORE DETAILS</span></div>
    </div>
    <div class="price-col">
      <div class="head"><h3>CLOUD</h3><span>Reduce Costs &amp; Increase Performance</span></div>
      <div class="row">Online Backup</div>
      <div class="row">Private Cloud Services</div>
      <div class="row">Virtual Desktop</div>
      <div class="foot"><span class="btn btn-blue">MORE DETAILS</span></div>
    </div>
  </div>
</section>

<section class="section contracts">
  <h2>NO LONG CONTRACTS!</h2>
  <p>We don't believe any small business should pay for IT Support you don't need. You shouldn't be overcharged just because you're not using the latest technology. If you're not happy with the service you're getting from your provider, you should be free to walk away. As a small business ourselves, we keep it honest. It's about time someone treated your business the way you would treat it.</p>
  <div class="call">Call us today on <span>01632 960 222</span></div>
</section>

<section class="section support-band" role="img" aria-label="Photo of a support team working together at desks">
  <div class="info-box info-left">
    <h2>TECHNICAL SUPPORT</h2>
    <p>Our highly skilled and certified engineers are on hand to support your business and will resolve your IT problems as quickly as possible. Our remote support service is 24/7 and problems are solved the first time. This kind of service is efficient, secure, easy and helps to keep your staff productive and your business running.</p>
  </div>
  <div class="info-box info-right">
    <h2>WE EXCEED EXPECTATIONS</h2>
    <p>At Bright Mend, IT Support is tailored to each client. Our managed service customers benefit from the latest tools and trained engineers who take the time to understand your systems. We make sure your technology works for you rather than against you, and we keep prices clear and simple. With no long contracts, we earn your trust every month by delivering service that goes above and beyond what you expect from a provider.</p>
  </div>
</section>

<section class="section map" role="img" aria-label="Map showing the office locations along the coast">
  <div class="offices">
    <div class="office"><h4>Riverside Office</h4><p>12 Harbour Lane<br>Riverside RS1 4AB</p></div>
    <div class="office"><h4>Northfield Office</h4><p>8 Mill Street<br>Northfield NF2 7CD</p></div>
    <div class="office"><h4>Support:</h4><p>support@brightmend.co.uk<br>t: 01632 960 222</p></div>
    <div class="office"><h4>Sales:</h4><p>sales@brightmend.co.uk<br>t: 01632 960 223</p></div>
  </div>
</section>

<section class="section contact">
  <div class="connect">
    <h2>Connect Us</h2>
    <div class="socials"><span></span><span></span><span></span><span></span><span></span></div>
    <div class="wordmark">BRIGHT MEND</div>
    <small>Copyright ©. All Right Reserved<br>Contact Us | Site Map | Terms Of Use | Privacy Policy</small>
  </div>
  <div class="contact-form">
    <h2>Contact Us</h2>
    <div class="fields">
      <div class="field">Name</div>
      <div class="field">Email Address</div>
      <div class="field message">Message</div>
    </div>
    <span class="btn">SEND NOW</span>
  </div>
  <div class="legal">v1.0</div>
</section>

</body>
</html>
```